Bright Path Mentors Needs A New Website Design

We need a 8 page website designed for "Bright Path Mentors .ca" similar in design to: "keystone learning hub .com".

The winner/successful candidate on the home page will be asked to complete the following inner pages to complete the project:

About Us
Philosophy
How We Work
Work With Us
Blog
Find A Tutor
Contact

Target Market(s)

Tutoring business clients/children

Industry/Entity Type

Education

Number of Pages Required

5+ page

Font styles to use
Sans Serif

Requirements
Must have
• The attached logo included of course. Similar design to the design provided above in the brief. Clear high quality high resolution images of children in school settings.

```html
<!DOCTYPE html>
<html lang="en">
<head>
<meta charset="utf-8">
<title>Bright Path Mentors — Home</title>
<link href="https://fonts.googleapis.com/css2?family=Roboto+Slab:wght@400;700&family=Raleway:wght@400;600;700&family=Libre+Baskerville:ital,wght@1,400;1,700&display=swap" rel="stylesheet">
<style>
:root{
  --blue:#2e3a8f;
  --blue-dark:#27307a;
  --orange:#f7941d;
  --orange-soft:#f9a441;
  --grey:#e9e9e9;
  --text:#555;
  --footer:#1c1c1c;
  --white:#fff;
}
*{box-sizing:border-box;margin:0;padding:0}
html,body{width:1200px;height:3203px;overflow:hidden}
body{font-family:'Raleway',sans-serif;color:var(--text);background:var(--white)}
.page{position:relative;width:1200px;height:3203px;overflow:hidden}
.abs{position:absolute}
.slab{font-family:'Roboto Slab',serif}

/* header */
.topbar{left:0;top:0;width:1200px;height:47px;background:var(--orange-soft)}
.topbar .promo{position:absolute;left:420px;top:11px;font:700 19px 'Roboto Slab',serif;color:#2a2a2a}
.social{position:absolute;display:flex;gap:8px}
.social span{width:30px;height:30px;border-radius:50%;border:2px solid currentColor;display:block}
.topbar .social{left:880px;top:8px;color:#2a2a2a}
.navbar{left:0;top:47px;width:1200px;height:85px;background:var(--blue);border-bottom:4px solid var(--orange)}
.nav{position:absolute;left:334px;top:34px;display:flex;gap:22px;font:400 15px 'Roboto Slab',serif;color:var(--white);text-transform:uppercase}
.logo-badge{left:98px;top:4px;width:172px;height:172px;border-radius:50%;background:var(--white);display:flex;align-items:center;justify-content:center;text-align:center;font:700 22px 'Roboto Slab',serif;color:var(--blue);line-height:1.2;box-shadow:0 2px 6px rgba(0,0,0,.2)}
.free-tab{left:1082px;top:0;width:118px;height:88px;background:var(--orange);color:var(--white);font:400 18px 'Roboto Slab',serif;text-align:center;padding-top:12px;line-height:1.3;clip-path:polygon(0 0,100% 0,100% 80%,50% 100%,0 80%)}

/* hero */
.hero{left:0;top:136px;width:1200px;height:547px;background:linear-gradient(100deg,#6b4a3a 0%,#a98a6e 35%,#c8b39a 60%,#8b6a52 100%)}
.hero-kicker{left:96px;top:258px;font:400 23px 'Roboto Slab',serif;color:var(--white)}
.hero-title{left:96px;top:300px;font:700 50px 'Roboto Slab',serif;color:var(--white)}
.btn-ghost{left:96px;top:384px;width:196px;height:48px;border:2px solid var(--white);border-radius:24px;color:var(--white);font:700 16px 'Roboto Slab',serif;display:flex;align-items:center;justify-content:center;background:rgba(255,255,255,.08)}
.arrow{color:var(--white)}
.feature{top:512px;height:128px;color:var(--white);display:flex;padding:26px 20px}
.feature.blue{background:rgba(46,58,143,.9)}
.feature.orange{background:rgba(247,148,29,.92)}
.feature h3{font:700 20px 'Roboto Slab',serif;line-height:1.35;text-transform:uppercase}
.feature p{font:700 16px 'Raleway',sans-serif;margin-top:10px}
.feature svg{flex:none;margin-right:18px;margin-top:10px}

/* about */
.section-title{font:700 29px 'Roboto Slab',serif;color:var(--blue);text-transform:uppercase}
.section-title em{font-style:normal;color:var(--orange)}
.rule{height:3px;background:var(--blue)}
.about-title{left:98px;top:722px}
.about-rule{left:98px;top:762px;width:96px}
.about-text{left:98px;top:786px;width:505px;font:400 13px/25px 'Raleway',sans-serif;color:#666}
.about-text p+p{margin-top:10px}
.btn-solid{background:var(--blue);color:var(--white);border-radius:22px;font:700 15px 'Raleway',sans-serif;display:flex;align-items:center;justify-content:center;text-transform:uppercase}
.chat-btn{left:98px;top:980px;width:164px;height:40px}
.video{left:694px;top:732px;width:402px;height:280px;background:linear-gradient(135deg,#dcd6c8,#c98f5c 55%,#5a6aa0);border:4px solid #ddd;box-shadow:0 6px 14px rgba(0,0,0,.25)}
.video-bar{position:absolute;left:0;bottom:0;width:100%;height:22px;background:rgba(30,30,40,.85)}
.play{position:absolute;left:176px;top:108px;width:52px;height:52px;border-radius:50%;background:rgba(255,255,255,.55)}

/* academic */
.academic{left:0;top:1061px;width:1200px;height:461px;background:var(--grey)}
.academic-title{left:0;top:1098px;width:1200px;text-align:center}
.academic-rule{left:555px;top:1146px;width:136px;height:2px}
.subject{top:1212px;width:200px;text-align:center;font:400 17px/27px 'Roboto Slab',serif;color:var(--blue)}
.subject .pin{width:140px;height:160px;margin:0 auto 14px;display:block}
.subject.active{color:var(--orange)}
.carousel-arrow{color:#333}

/* why */
.why{left:0;top:1522px;width:1200px;height:532px;background:linear-gradient(180deg,#2c3a93,#24307f)}
.why-title{left:0;top:1562px;width:1200px;text-align:center;font:700 27px 'Roboto Slab',serif;color:var(--white);text-transform:uppercase}
.why-item{width:300px;color:var(--white)}
.why-item h4{font:400 24px 'Roboto Slab',serif;margin-bottom:10px}
.why-item p{font:400 13px/21px 'Raleway',sans-serif}
.why-item.left{text-align:right}
.why-icon{width:64px;height:64px;border-radius:50%;background:var(--orange);display:flex;align-items:center;justify-content:center}
.shield-text{left:464px;top:1710px;width:276px;text-align:center}
.shield-text h3{font:700 italic 25px/34px 'Libre Baskerville',serif;color:var(--blue)}
.shield-text p{font:400 13px/24px 'Raleway',sans-serif;color:#555;margin-top:14px}
.shield-btn{display:inline-block;margin-top:18px;background:var(--orange);color:var(--white);font:700 14px 'Raleway',sans-serif;padding:11px 18px}

/* testimonials */
.testimonials{left:0;top:2054px;width:1200px;height:397px;background:#ececec}
.testi-title{left:0;top:2104px;width:1200px;text-align:center}
.testi-rule{left:520px;top:2150px;width:110px;height:2px}
.quote{left:180px;top:2192px;width:840px;text-align:center;font:400 italic 20px/40px 'Libre Baskerville',serif;color:var(--orange)}
.qmark{font:700 64px 'Libre Baskerville',serif;color:var(--blue)}
.author{left:0;top:2306px;width:1200px;text-align:center;font:400 18px 'Raleway',sans-serif;color:#333}
.author small{font-size:12px;text-transform:uppercase}
.more-btn{left:488px;top:2352px;width:222px;height:46px}

/* inquiry */
.inquiry{left:0;top:2451px;width:1200px;height:356px;background:linear-gradient(180deg,#f7941d,#f6a23c 60%,#f7941d)}
.inquiry-title{left:0;top:2490px;width:1200px;text-align:center;font:700 29px 'Roboto Slab',serif;color:var(--white);text-transform:uppercase}
.inquiry-rule{left:550px;top:2535px;width:100px;height:2px;background:var(--white)}
.field{height:40px;border:1px solid rgba(255,255,255,.85);color:var(--white);font:400 14px 'Raleway',sans-serif;padding:11px 10px;background:rgba(255,255,255,.06)}
.inquiry-btn{left:459px;top:2716px;width:286px;height:44px;background:var(--blue);color:var(--white);font:700 14px 'Raleway',sans-serif;display:flex;align-items:center;justify-content:center;text-transform:uppercase}

/* footer */
.footer{left:0;top:2807px;width:1200px;height:336px;background:var(--footer)}
.footer-name{left:96px;top:2920px;width:172px;text-align:center;font:700 26px/34px 'Roboto Slab',serif;color:var(--white);text-transform:uppercase}
.footer h5{position:absolute;font:700 17px 'Roboto Slab',serif;color:var(--white);text-transform:uppercase}
.quick{left:372px;top:2898px;list-style:none;font:400 14px/32px 'Raleway',sans-serif;color:var(--white)}
.contact-row{left:566px;width:220px;display:flex;gap:16px;color:var(--white);font:400 13px/20px 'Raleway',sans-serif}
.contact-row b{display:block;font-weight:700;font-size:14px}
.c-icon{flex:none;width:36px;height:36px;border-radius:50%;background:var(--white);display:flex;align-items:center;justify-content:center}
.f-field{background:#111;border:1px solid #777;color:var(--white);font:400 12px 'Raleway',sans-serif;padding:10px 10px}
.f-submit{left:813px;top:3059px;width:120px;height:38px;background:var(--orange);color:var(--white);font:700 12px 'Raleway',sans-serif;display:flex;align-items:center;justify-content:center;text-transform:uppercase}
.bottombar{left:0;top:3143px;width:1200px;height:60px;background:var(--orange)}
.copy{position:absolute;left:96px;top:21px;font:400 14px 'Raleway',sans-serif;color:#3a2a10}
.cards{position:absolute;left:706px;top:17px;display:flex;gap:8px}
.cards span{width:46px;height:26px;background:var(--white);border-radius:3px;display:block}
.cards span:first-child{width:68px}
.bottombar .social{left:946px;top:15px;color:var(--white)}
</style>
</head>
<body>
<div class="page">

  <!-- header -->
  <div class="abs topbar">
    <div class="promo">"First Session Just $35 - Call 1-855-555-0147 Now"</div>
    <div class="social" aria-label="Social links"><span></span><span></span><span></span><span></span><span></span></div>
  </div>
  <div class="abs navbar">
    <nav class="nav"><span>Home</span><span>About Us</span><span>Philosophy</span><span>How We Work</span><span>Work With Us</span><span>Blog</span><span>Find A Tutor</span><span>Contact</span></nav>
  </div>
  <div class="abs logo-badge">Bright Path<br>Mentors</div>
  <div class="abs free-tab">Free<br>Assessment</div>

  <!-- hero -->
  <div class="abs hero" role="img" aria-label="Photo of happy children raising hands in a classroom"></div>
  <svg class="abs arrow" style="left:24px;top:380px" width="30" height="52" viewBox="0 0 30 52"><path d="M26 2 4 26l22 24" fill="none" stroke="#fff" stroke-width="3"/></svg>
  <svg class="abs arrow" style="left:1146px;top:380px" width="30" height="52" viewBox="0 0 30 52"><path d="M4 2l22 24L4 50" fill="none" stroke="#fff" stroke-width="3"/></svg>
  <div class="abs hero-kicker">BETTER EDUCATION FOR A</div>
  <div class="abs hero-title">BETTER WORLD</div>
  <div class="abs btn-ghost">LEARN WITH US</div>

  <div class="abs feature blue" style="left:96px;width:324px">
    <svg width="52" height="44" viewBox="0 0 52 44"><path d="M26 4 2 15l24 11 24-11z" fill="#fff"/><path d="M12 21v11c6 6 22 6 28 0V21l-14 6z" fill="#fff"/><path d="M46 16v14" stroke="#fff" stroke-width="2"/></svg>
    <div><h3>Making Parents &amp;<br>Kids Happy</h3><p>Our Reviews</p></div>
  </div>
  <div class="abs feature orange" style="left:438px;width:320px">
    <svg width="52" height="44" viewBox="0 0 52 44"><rect x="4" y="4" width="44" height="30" fill="none" stroke="#fff" stroke-width="3"/><circle cx="16" cy="20" r="5" fill="#fff"/><path d="M28 14h14M28 22h10" stroke="#fff" stroke-width="3"/><path d="M18 34v8M34 34v8" stroke="#fff" stroke-width="3"/></svg>
    <div><h3>Tutoring With A<br>Personal Touch</h3><p>How We Work</p></div>
  </div>
  <div class="abs feature blue" style="left:775px;width:325px">
    <svg width="52" height="44" viewBox="0 0 52 44"><rect x="6" y="4" width="40" height="30" fill="none" stroke="#fff" stroke-width="3"/><path d="M14 14h24M14 22h14" stroke="#fff" stroke-width="3"/><circle cx="36" cy="32" r="7" fill="#fff"/></svg>
    <div><h3>Satisfaction<br>Guranteed</h3><p>Find Your Tutor</p></div>
  </div>

  <!-- about -->
  <h2 class="abs section-title about-title">About <em>BrightPathMentors</em></h2>
  <div class="abs rule about-rule"></div>
  <div class="abs about-text">
    <p>Maya found her passion for teaching as a high school student. She spent her summer and evenings tutoring the students in her neighborhood. Watching her students grow and succeed by giving them encouragement and specific strategies is what fostered her love of learning. Maya went on to complete.</p>
    <p>After graduating from her Masters in Education from the University of Lakeview she moved back to Toronto and began working along side a tutoring agency in charge of running a region in the GTA.</p>
  </div>
  <div class="abs btn-solid chat-btn">Start Chatting</div>
  <div class="abs video" role="img" aria-label="Video still of a cartoon teacher with pupils at a chalkboard">
    <div class="play"></div>
    <div class="video-bar"></div>
  </div>

  <!-- academic tutoring -->
  <div class="abs academic"></div>
  <h2 class="abs section-title academic-title">Academic <em>Tutoring</em></h2>
  <div class="abs rule academic-rule"></div>
  <svg class="abs carousel-arrow" style="left:34px;top:1258px" width="20" height="40" viewBox="0 0 20 40"><path d="M18 2 2 20l16 18" fill="none" stroke="#333" stroke-width="2"/></svg>
  <svg class="abs carousel-arrow" style="left:1146px;top:1258px" width="20" height="40" viewBox="0 0 20 40"><path d="M2 2l16 18L2 38" fill="none" stroke="#333" stroke-width="2"/></svg>

  <div class="abs subject" style="left:81px">
    <svg class="pin" viewBox="0 0 140 160"><path d="M70 4a66 66 0 0 1 14 130l-14 18-14-18A66 66 0 0 1 70 4z" fill="#fff" stroke="#2e3a8f" stroke-width="3"/><path d="M44 58 70 44l26 14zM46 62h48v4H46zM50 68h6v22h-6zM62 68h6v22h-6zM74 68h6v22h-6zM86 68h6v22h-6zM44 92h52v6H44z" fill="#2e3a8f"/></svg>
    JK to Grade 12
  </div>
  <div class="abs subject active" style="left:291px">
    <svg class="pin" viewBox="0 0 140 160"><path d="M70 4a66 66 0 0 1 14 130l-14 18-14-18A66 66 0 0 1 70 4z" fill="#f7941d" stroke="#f7941d" stroke-width="3"/><circle cx="70" cy="70" r="58" fill="none" stroke="#fff" stroke-width="2"/><path d="M44 50h50v12H44zM40 66h56v12H40zM46 82h50v12H46z" fill="none" stroke="#fff" stroke-width="3"/></svg>
    All Subjects - Math,<br>English, French,<br>Science and More!
  </div>
  <div class="abs subject" style="left:498px">
    <svg class="pin" viewBox="0 0 140 160"><path d="M70 4a66 66 0 0 1 14 130l-14 18-14-18A66 66 0 0 1 70 4z" fill="#fff" stroke="#2e3a8f" stroke-width="3"/><path d="M70 46 38 60l32 14 32-14z" fill="#2e3a8f"/><path d="M52 68v14c10 8 26 8 36 0V68l-18 8z" fill="#2e3a8f"/><path d="M98 62v18" stroke="#2e3a8f" stroke-width="3"/></svg>
    We Work With Your<br>Student's Current<br>Class Curriculum
  </div>
  <div class="abs subject" style="left:707px">
    <svg class="pin" viewBox="0 0 140 160"><path d="M70 4a66 66 0 0 1 14 130l-14 18-14-18A66 66 0 0 1 70 4z" fill="#fff" stroke="#2e3a8f" stroke-width="3"/><rect x="48" y="40" width="40" height="54" fill="none" stroke="#2e3a8f" stroke-width="3"/><path d="M54 54l4 4 6-8M54 70l4 4 6-8M54 86l4 4 6-8M68 56h14M68 72h14M68 88h14" fill="none" stroke="#2e3a8f" stroke-width="3"/></svg>
    ACT/SAT Test<br>Prep
  </div>
  <div class="abs subject" style="left:910px">
    <svg class="pin" viewBox="0 0 140 160"><path d="M70 4a66 66 0 0 1 14 130l-14 18-14-18A66 66 0 0 1 70 4z" fill="#fff" stroke="#2e3a8f" stroke-width="3"/><circle cx="70" cy="58" r="8" fill="none" stroke="#2e3a8f" stroke-width="4"/><circle cx="50" cy="64" r="7" fill="none" stroke="#2e3a8f" stroke-width="4"/><circle cx="90" cy="64" r="7" fill="none" stroke="#2e3a8f" stroke-width="4"/><path d="M56 88c0-12 28-12 28 0M38 90c0-10 18-10 18-4M102 90c0-10-18-10-18-4" fill="none" stroke="#2e3a8f" stroke-width="4"/></svg>
    In-Home Tutoring<br>We Come to You
  </div>

  <!-- why -->
  <div class="abs why"></div>
  <h2 class="abs why-title">Why Bright Path Mentors?</h2>
  <svg class="abs" style="left:444px;top:1672px" width="314" height="368" viewBox="0 0 314 368"><path d="M157 4C110 22 58 24 6 18v170c0 90 80 150 151 176 71-26 151-86 151-176V18c-52 6-104 4-151-14z" fill="#fff" stroke="#2e3a8f" stroke-width="3"/><path d="M157 14C114 30 66 32 16 28v160c0 82 74 138 141 162 67-24 141-80 141-162V28c-50 4-98 2-141-14z" fill="none" stroke="#2e3a8f" stroke-width="1.5"/></svg>
  <div class="abs shield-text">
    <h3>Highly Credentialed Tutors</h3>
    <p>We require the most rigorous qualifications of our tutors, in addition to a background check.</p>
    <span class="shield-btn">Read More</span>
  </div>

  <div class="abs why-item left" style="left:56px;top:1706px"><h4>Certified Teachers</h4><p>After graduating from her Masters in Education from the University of Lakeview she moved back to Toronto</p></div>
  <div class="abs why-icon" style="left:358px;top:1710px"><svg width="34" height="30" viewBox="0 0 34 30"><rect x="2" y="2" width="30" height="20" fill="none" stroke="#fff" stroke-width="2.5"/><circle cx="10" cy="13" r="4" fill="#fff"/><path d="M18 9h10M18 15h8" stroke="#fff" stroke-width="2.5"/></svg></div>
  <div class="abs why-item left" style="left:56px;top:1844px"><h4>Flexible In Tutoring</h4><p>After graduating from her Masters in Education from the University of Lakeview she moved back to Toronto</p></div>
  <div class="abs why-icon" style="left:358px;top:1848px"><svg width="30" height="34" viewBox="0 0 30 34"><circle cx="15" cy="9" r="7" fill="#fff"/><path d="M2 32c0-12 26-12 26 0z" fill="#fff"/></svg></div>

  <div class="abs why-icon" style="left:778px;top:1710px"><svg width="30" height="34" viewBox="0 0 30 34"><circle cx="15" cy="9" r="7" fill="#fff"/><path d="M2 32c0-12 26-12 26 0z" fill="#fff"/></svg></div>
  <div class="abs why-item" style="left:862px;top:1706px"><h4>Personal Attention</h4><p>After graduating from her Masters in Education from the University of Lakeview she moved back to Toronto</p></div>
  <div class="abs why-icon" style="left:778px;top:1848px"><svg width="30" height="30" viewBox="0 0 30 30"><path d="M4 13h6v15H4zM12 13l6-11c4 0 4 4 3 8h7c2 0 3 2 2 4l-3 12c-1 2-2 2-4 2H12z" fill="#fff"/></svg></div>
  <div class="abs why-item" style="left:862px;top:1844px"><h4>Tutor Gurantee</h4><p>After graduating from her Masters in Education from the University of Lakeview she moved back to Toronto</p></div>

  <!-- testimonials -->
  <div class="abs testimonials"></div>
  <h2 class="abs section-title testi-title">Read Our <em>&nbsp;Testimonials</em></h2>
  <div class="abs rule testi-rule"></div>
  <div class="abs qmark" style="left:164px;top:2166px">&ldquo;</div>
  <div class="abs quote">Maya Delorme Dear Ms. Delorme: RE: Highest Recommendation for Tutoring Services<br>I take this opportunity to give the highest...</div>
  <div class="abs qmark" style="left:946px;top:2230px">&rdquo;</div>
  <div class="abs author">Lena P. <small>(Vaughan, Ontario)</small></div>
  <div class="abs btn-solid more-btn">Read More Testimonials</div>

  <!-- inquiry -->
  <div class="abs inquiry"></div>
  <h2 class="abs inquiry-title">General Inquiry Form</h2>
  <div class="abs inquiry-rule"></div>
  <div class="abs field" style="left:166px;top:2587px;width:282px">Name</div>
  <div class="abs field" style="left:459px;top:2587px;width:282px">Email</div>
  <div class="abs field" style="left:751px;top:2587px;width:284px">Telephone</div>
  <div class="abs field" style="left:166px;top:2647px;width:282px">Postal Code</div>
  <div class="abs field" style="left:459px;top:2647px;width:282px">Iam a:<svg style="position:absolute;right:12px;top:16px" width="10" height="6" viewBox="0 0 10 6"><path d="M0 0h10L5 6z" fill="#fff"/></svg></div>
  <div class="abs field" style="left:751px;top:2647px;width:284px">Message</div>
  <div class="abs inquiry-btn">Contact Bright Path Mentors</div>

  <!-- footer -->
  <div class="abs footer">
    <h5 style="left:372px;top:34px">Quick Links</h5>
    <h5 style="left:566px;top:34px">Contact Us</h5>
    <h5 style="left:813px;top:34px">Work With Us</h5>
  </div>
  <div class="abs footer-name">Bright Path<br>Mentors</div>
  <ul class="abs quick">
    <li>› Home</li><li>› About Us</li><li>› Philosophy</li><li>› How We Work</li><li>› Work With Us</li><li>› Contact Us</li>
  </ul>
  <div class="abs contact-row" style="top:2906px">
    <span class="c-icon"><svg width="14" height="18" viewBox="0 0 14 18"><path d="M7 0a7 7 0 0 1 7 7c0 5-7 11-7 11S0 12 0 7a7 7 0 0 1 7-7z" fill="#1c1c1c"/><circle cx="7" cy="7" r="2.5" fill="#fff"/></svg></span>
    <div><b>BRIGHTPATHMENTORS,</b>1200 Maple Ave #210,<br>North York, ON M2N</div>
  </div>
  <div class="abs contact-row" style="top:2988px">
    <span class="c-icon"><svg width="12" height="18" viewBox="0 0 12 18"><rect x="1" y="1" width="10" height="16" rx="2" fill="none" stroke="#1c1c1c" stroke-width="2"/></svg></span>
    <div><b>PHONE:</b>1-855-555-0147</div>
  </div>
  <div class="abs contact-row" style="top:3052px">
    <span class="c-icon"><svg width="18" height="13" viewBox="0 0 18 13"><rect x="1" y="1" width="16" height="11" fill="#1c1c1c"/><path d="M1 1l8 6 8-6" fill="none" stroke="#fff" stroke-width="1.5"/></svg></span>
    <div><b>Mail:</b>info@brightpathmentors.ca</div>
  </div>
  <div class="abs f-field" style="left:813px;top:2906px;width:138px;height:36px">Name</div>
  <div class="abs f-field" style="left:961px;top:2906px;width:140px;height:36px">Phone</div>
  <div class="abs f-field" style="left:813px;top:2950px;width:288px;height:36px">Upload Resume<svg style="position:absolute;right:10px;top:10px" width="16" height="14" viewBox="0 0 16 14"><circle cx="7" cy="4" r="3.5" fill="#fff"/><path d="M1 14c0-6 12-6 12 0z" fill="#fff"/><path d="M13 3v6M10 6h6" stroke="#fff" stroke-width="1.6"/></svg></div>
  <div class="abs f-field" style="left:813px;top:2994px;width:288px;height:58px">Message</div>
  <div class="abs f-submit">Submit Now</div>

  <div class="abs bottombar">
    <div class="copy">Copyright © 2016 Bright Path Mentors. All Right Reserved</div>
    <div class="cards" aria-label="Accepted payment methods"><span></span><span></span><span></span></div>
    <div class="social" aria-label="Social links"><span></span><span></span><span></span><span></span></div>
  </div>

</div>
</body>
</html>
```